Exciting letterhead design for startup company

We need a A4 letterhead designing.

See attached file which contains the logo (on 3 different coloured backgrounds) and then the address and contact information. It also contains 4 colours that can be used.

Looking for an imaginative design. We are a young, fresh startup website design company so need a letterhead that reflects our industry.

Sans Serif

```html
<!DOCTYPE html>
<html lang="en">
<head>
<meta charset="utf-8">
<title>PixelNest Letterhead</title>
<link rel="stylesheet" href="https://fonts.googleapis.com/css2?family=Open+Sans:wght@400;700&display=swap">
<style>
  :root {
    --backdrop: #ececec;
    --paper: #ffffff;
    --ink: #1a1a1a;
    --ink-soft: #555b5f;
    --brand-blue: #0a8ed8;
    --brand-slate: #37434a;
    --logo-block: #1b1816;
  }
  * { box-sizing: border-box; margin: 0; padding: 0; }
  html, body {
    width: 1200px;
    height: 1006px;
    overflow: hidden;
    background: var(--backdrop);
    font-family: "Open Sans", Arial, sans-serif;
  }
  .letterhead {
    position: absolute;
    left: 267px;
    top: 33px;
    width: 666px;
    height: 940px;
    background: var(--paper);
    box-shadow: 0 8px 24px rgba(0,0,0,0.12);
    overflow: hidden;
  }
  .brand {
    position: absolute;
    left: 44px;
    top: 48px;
  }
  .brand-block {
    display: flex;
    align-items: center;
    justify-content: center;
    width: 176px;
    height: 52px;
    background: var(--logo-block);
    color: #ffffff;
    font-size: 27px;
    font-weight: 400;
    letter-spacing: -0.5px;
  }
  .contact-line {
    display: flex;
    gap: 10px;
    margin-top: 5px;
    font-size: 9.5px;
    color: var(--ink-soft);
  }
  .contact-item {
    display: flex;
    align-items: center;
    gap: 3px;
  }
  .contact-item svg { width: 9px; height: 9px; fill: var(--brand-blue); }
  .company-details {
    position: absolute;
    right: 40px;
    top: 44px;
    text-align: right;
    font-style: normal;
    font-size: 8.5px;
    line-height: 1.35;
    color: var(--ink-soft);
  }
  .company-name {
    font-size: 12px;
    font-weight: 700;
    font-style: normal;
    color: var(--ink);
    margin-bottom: 2px;
  }
  .footer-rule {
    position: absolute;
    left: 0;
    bottom: 0;
    width: 666px;
    height: 10px;
    background: var(--brand-slate);
  }
</style>
</head>
<body>
  <main class="letterhead">
    <header>
      <div class="brand">
        <div class="brand-block">PixelNest</div>
        <div class="contact-line">
          <span class="contact-item">
            <svg viewBox="0 0 10 10" aria-hidden="true"><path d="M2 0.5 L3.6 2.6 L2.8 3.6 Q4 6 6.4 7.2 L7.4 6.4 L9.5 8 L8.4 9.5 Q2 8.5 0.5 1.6 Z"/></svg>
            0800 123 4567
          </span>
          <span class="contact-item">
            <svg viewBox="0 0 10 10" aria-hidden="true"><path d="M0.5 2 H9.5 V8 H0.5 Z M1 2.4 L5 5.4 L9 2.4" stroke="#fff" stroke-width="0.6"/></svg>
            hello@pixelnest.co.uk
          </span>
        </div>
      </div>
      <address class="company-details">
        <div class="company-name">PixelNest Limited</div>
        Suite 4, Harbour Court, Leeds LS1 2AB<br>
        Registered in England &amp; Wales<br>
        Company No. 0123 4567
      </address>
    </header>
    <div class="footer-rule" aria-hidden="true"></div>
  </main>
</body>
</html>
```